Web design project for exciting Australian start-up

Background
We are looking for a creative and talented web design artist to work alongside our market leading web developer.
• You will be required to create a modern and clean design theme for our website, incorporating selected rustic colour scheme elements for our exciting Australian start-up to operate within the coffee industry.
reoccurring work to be expected to flow to the successful designer.
Requirements
• c. 5 - 10 page website
• Landing page
• Log in/ out
• 404 template
• Typography is emphasised
• Please use either a) typemarrow.com, b) free web fonts, c) brindle fonts
• All design elements in vector format
• Preferably with icons for each header title(i.e. about us, how it works etc) but designer have free reign over how the site looks, so might not be applicable
• All pages to be responsive
• Down to eSlab resolution

High level visual design brief attached - additional pages to be worked from base design.

Design inspiration
• We would like to use design elements from the following sources:
http://www.zandrix.com/halcyon/ (Functionality)
Colour scheme refer to logo and complementary style guide

```html
<!DOCTYPE html>
<html lang="en">
<head>
<meta charset="utf-8">
<title>Brewhaven — Coffee Marketplace</title>
<link rel="stylesheet" href="https://fonts.googleapis.com/css2?family=Arvo&family=Mulish:wght@400;700;800&family=Open+Sans:wght@300;700&display=swap">
<style>
  :root {
    --orange: #fb9f35;
    --red: #ea3f3f;
    --ink: #222222;
    --text: #555555;
    --nav-active: #f4f4f4;
    --rule: #ececec;
    --footer-bg: #e8e8e8;
    --bar-bg: #4b4b4b;
    --bar-rule: #6a6a6a;
    --white: #ffffff;
  }
  * { margin: 0; padding: 0; box-sizing: border-box; }
  html, body { width: 1200px; height: 950px; overflow: hidden; background: var(--white); }
  body { position: relative; font-family: "Mulish", sans-serif; color: var(--text); }

  .site-header { position: absolute; left: 0; top: 0; width: 1200px; height: 107px; background: var(--white); }
  .brand { position: absolute; left: 161px; top: 33px; display: flex; align-items: center; gap: 10px;
    font-family: "Mulish", sans-serif; font-weight: 800; font-size: 25px; letter-spacing: 1px; color: var(--ink); }
  .brand-dot { width: 34px; height: 34px; border-radius: 50%; background: var(--orange); }

  .main-nav { position: absolute; top: 0; left: 560px; height: 107px; display: flex; }
  .nav-item { height: 107px; display: flex; flex-direction: column; align-items: center; justify-content: center;
    gap: 6px; border-right: 1px solid var(--rule); font-size: 12px; color: #444; text-transform: uppercase; padding-top: 4px; }
  .nav-item:first-child { border-left: 1px solid var(--rule); }
  .nav-item.is-active { background: var(--nav-active); }
  .nav-item svg { width: 20px; height: 20px; }
  .nav-about { width: 94px; }
  .nav-how { width: 135px; }
  .nav-faq { width: 66px; }

  .btn { position: absolute; display: flex; align-items: center; justify-content: center; color: var(--white);
    font-size: 14px; border-radius: 2px; }
  .btn-login { left: 878px; top: 38px; width: 75px; height: 31px; background: var(--orange); }
  .btn-signup { left: 963px; top: 38px; width: 75px; height: 31px; background: var(--red); }

  .hero { position: absolute; left: 0; top: 107px; width: 1200px; height: 543px;
    background: radial-gradient(ellipse at 50% 45%, #7a4a33 0%, #5a3220 45%, #2e170d 100%); }
  .hero-kicker { position: absolute; left: 0; width: 1200px; top: 210px; text-align: center;
    font-family: "Open Sans", sans-serif; font-weight: 300; font-size: 22px; color: var(--white); }
  .hero-title { position: absolute; left: 0; width: 1200px; top: 240px; text-align: center;
    font-family: "Open Sans", sans-serif; font-weight: 700; font-size: 37px; color: var(--white); }
  .hero-cta { position: absolute; left: 519px; top: 302px; width: 162px; height: 45px; background: var(--orange);
    color: var(--white); font-size: 17px; display: flex; align-items: center; justify-content: center; }
  .slide-arrow { position: absolute; top: 240px; width: 57px; height: 57px; }
  .slide-prev { left: 161px; }
  .slide-next { left: 981px; }

  .site-footer { position: absolute; left: 0; top: 650px; width: 1200px; height: 236px; background: var(--footer-bg); }
  .footer-col { position: absolute; top: 50px; }
  .footer-col h3 { font-family: "Arvo", serif; font-weight: 400; font-size: 17px; color: var(--ink); letter-spacing: .5px; margin-bottom: 14px; }
  .footer-col li { list-style: none; font-size: 14px; color: var(--text); height: 31px; display: flex; align-items: center; }
  .col-info { left: 295px; }
  .col-who { left: 541px; }
  .col-who li, .col-join li { padding-left: 2px; }
  .col-join { left: 797px; }
  .social-name { width: 76px; }
  .social-dot { width: 9px; height: 9px; border-radius: 50%; background: #555; }

  .bottom-bar { position: absolute; left: 0; top: 886px; width: 1200px; height: 64px; background: var(--bar-bg); }
  .bottom-bar .rule { position: absolute; left: 161px; top: 5px; width: 877px; height: 1px; background: var(--bar-rule); }
  .copyright { position: absolute; left: 0; width: 1200px; top: 22px; text-align: center; font-size: 14px; color: var(--white); }
</style>
</head>
<body>
  <header class="site-header">
    <div class="brand"><span>BREWHAVEN</span><span class="brand-dot"></span></div>
    <nav class="main-nav">
      <div class="nav-item nav-about is-active">
        <svg viewBox="0 0 20 20" fill="none" stroke="#fb9f35" stroke-width="1.4"><path d="M3 10 L10 3 L17 10"/><path d="M5 8.5 V17 H15 V8.5"/><path d="M8.5 17 V12.5 H11.5 V17"/></svg>
        <span>About us</span>
      </div>
      <div class="nav-item nav-how">
        <svg viewBox="0 0 20 20" fill="none" stroke="#777" stroke-width="1.3"><circle cx="8" cy="8" r="3"/><path d="M2.5 18 C3 13.5 13 13.5 13.5 18"/><rect x="12" y="2" width="6" height="5"/></svg>
        <span>How it works</span>
      </div>
      <div class="nav-item nav-faq">
        <svg viewBox="0 0 20 20" fill="none" stroke="#777" stroke-width="1.3"><rect x="4" y="6" width="3" height="11"/><rect x="9" y="3" width="3" height="14"/><rect x="14" y="8" width="3" height="9"/></svg>
        <span>FAQ</span>
      </div>
    </nav>
    <a class="btn btn-login">Login</a>
    <a class="btn btn-signup">Sign up</a>
  </header>

  <section class="hero" role="img" aria-label="Close-up photograph of roasted coffee beans and ground coffee">
    <p class="hero-kicker">AUSTRALIA FIRST ONLINE</p>
    <h1 class="hero-title">COFFEE MARKETPLACE</h1>
    <a class="hero-cta">Watch Video</a>
    <svg class="slide-arrow slide-prev" viewBox="0 0 57 57" fill="none" stroke="#fff" stroke-width="2.5"><circle cx="28.5" cy="28.5" r="27"/><path d="M31 22 L25 28.5 L31 35"/></svg>
    <svg class="slide-arrow slide-next" viewBox="0 0 57 57" fill="none" stroke="#fff" stroke-width="2.5"><circle cx="28.5" cy="28.5" r="27"/><path d="M26 22 L32 28.5 L26 35"/></svg>
  </section>

  <footer class="site-footer">
    <div class="footer-col col-info">
      <h3>HELPFUL INFO</h3>
      <ul><li>About Us</li><li>Media Enquiries</li><li>Terms &amp; Conditions</li><li>Privacy Policy</li></ul>
    </div>
    <div class="footer-col col-who">
      <h3>WHO WE ARE</h3>
      <ul><li>How it works</li><li>FAQ</li><li>Contact us</li></ul>
    </div>
    <div class="footer-col col-join">
      <h3>JOIN US ON</h3>
      <ul>
        <li><span class="social-name">Facebase</span><span class="social-dot"></span></li>
        <li><span class="social-name">Chirper</span><span class="social-dot"></span></li>
        <li><span class="social-name">Linkwork</span><span class="social-dot"></span></li>
        <li><span class="social-name">ViewTube</span><span class="social-dot"></span></li>
      </ul>
    </div>
  </footer>

  <div class="bottom-bar">
    <div class="rule"></div>
    <p class="copyright">Copyright © 2014 Brewhaven</p>
  </div>
</body>
</html>
```